Equipment Finance Specialist I work with companies who need the funds to buy their equipment

I would like a business card that stands out on the shelves. I want to be able to hand it to someone and say WOW. This card should have my logo.
You can put color into it I am very open on design and color

What my company does is we deal with dealerships that sell equipment such as Dump Trucks garbage trucks tractors trailers. Customers get referred to us and depending on their time in business we will ask for the following items

Companies that have been in business for more than two years we have a credit application program up to 250K . With this program we need the following items Credit application filled out(which is what I would like to be able for the customer to click on my website to get.) as well as three current month bank statements.

Deals over 250k we will need the following items

2 years business tax returns
2 years personal tax returns
Profit & Loss statement
Personal Financial Statement

what we do
100% FINANCING
SEASONAL PAYMENTS
LOAN BALLOON PAYMENTS
TRAC LEASING
LOW-INTEREST REFINANCING RATES
DEBT CONSOLIDATION

We specialize in creative financing solutions and offer a variety of reliable, flexible and expandable lending choices.

Target Market(s)

Trucking Companies

Industry/Entity Type

Trucking Company

Contact Information for Business Card

* $250,000 Application only Program
* Loans from $30,000 to 5,000,000
* Competitive Interest Rates

Font styles to use
Serif
Sans Serif

Colors

Designer to choose colors to be used in the design.

Requirements
Must have
• On the back of the card.
• * $250,000 Application only Program
• * Loans from $30,000 to 5,000,000
• My name, email, website. address
• * Competitive Interest Rates
• * 100% Financing
Nice to have
• I want my logo to pop on the card
• My logo is the great one I would like to use
Should not have
• I am up for your creativity as well

```html
<!DOCTYPE html>
<html lang="en">
<head>
<meta charset="utf-8">
<title>Summit Capital – Business Card</title>
<link href="https://fonts.googleapis.com/css2?family=Open+Sans:wght@400;600;700&family=Libre+Baskerville:wght@700&display=swap" rel="stylesheet">
<style>
  :root {
    --bg: #ece9e4;
    --asphalt: #1d1d1d;
    --asphalt-light: #2e2e2e;
    --navy: #26397a;
    --navy-deep: #1d2d64;
    --red: #e0283f;
    --red-light: #ea4a5e;
    --white: #ffffff;
    --silver: #c9cbce;
  }
  * { box-sizing: border-box; margin: 0; padding: 0; }
  html, body { width: 1200px; height: 900px; overflow: hidden; }
  body {
    background: var(--bg);
    font-family: "Open Sans", Arial, sans-serif;
    position: relative;
  }
  .card {
    position: absolute;
    left: 250px;
    width: 700px;
    height: 400px;
    overflow: hidden;
    box-shadow: 0 8px 24px rgba(0,0,0,.18);
  }
  .card--front { top: 36px; }
  .card--back { top: 464px; }

  .card__texture {
    position: absolute; inset: 0;
    background: radial-gradient(ellipse at 40% 40%, var(--asphalt-light), var(--asphalt) 75%);
  }
  .front__blue {
    position: absolute; inset: 0;
    background: linear-gradient(160deg, var(--navy), var(--navy-deep));
    clip-path: polygon(300px 0, 700px 0, 700px 280px, 420px 280px, 470px 120px);
  }
  .front__logo-tab {
    position: absolute; top: 0; right: 0;
    width: 440px; height: 110px;
    background: var(--white);
    clip-path: polygon(0 60px, 30px 0, 440px 0, 440px 110px, 46px 110px);
    display: flex; align-items: center; justify-content: center;
    padding-left: 40px; gap: 12px;
  }
  .logo-mark {
    width: 38px; height: 38px; border-radius: 50%;
    background: var(--navy);
  }
  .logo-name {
    font-weight: 700; font-size: 30px; letter-spacing: 1px;
    color: var(--navy); text-transform: uppercase;
  }
  .front__offers {
    position: absolute; left: 40px; top: 150px;
    list-style: none; color: var(--white);
    font-size: 18px; line-height: 27px; font-weight: 600;
  }
  .front__person {
    position: absolute; right: 40px; top: 188px;
    text-align: center; color: var(--white);
  }
  .person-name {
    font-family: "Libre Baskerville", Georgia, serif;
    font-size: 24px; letter-spacing: .5px;
  }
  .person-role { font-size: 18px; margin-top: 2px; }

  .contact-band {
    position: absolute; left: 0; right: 0; bottom: 0; height: 110px;
    background: linear-gradient(90deg, var(--red), var(--red-light));
    display: flex; padding: 22px 40px 0; gap: 60px;
  }
  .contact-col { list-style: none; }
  .contact-col li {
    display: flex; align-items: center; gap: 10px;
    color: var(--white); font-size: 18px; line-height: 30px; font-weight: 600;
  }
  .contact-col svg { width: 16px; height: 16px; flex: none; }

  .back__band {
    height: 96px; right: auto; width: 470px;
    clip-path: polygon(0 0, 100% 0, 93% 100%, 0 100%);
  }
  .back__address {
    position: absolute; left: 40px; bottom: 110px; list-style: none;
  }
  .back__logo {
    position: absolute; right: 56px; top: 120px;
    display: flex; align-items: center; gap: 16px;
  }
  .back__logo .logo-mark { width: 90px; height: 90px; background: var(--silver); }
  .back__logo .logo-name { color: var(--silver); font-size: 40px; }
</style>
</head>
<body>

  <section class="card card--front" aria-label="Card front">
    <div class="card__texture"></div>
    <div class="front__blue"></div>
    <div class="front__logo-tab">
      <span class="logo-mark"></span>
      <span class="logo-name">Summit Capital</span>
    </div>
    <ul class="front__offers">
      <li>$250,000 Application only Program</li>
      <li>Loans from $30,000 to 5,000,000</li>
      <li>Competitive Interest Rates</li>
      <li>100% Financing</li>
    </ul>
    <div class="front__person">
      <p class="person-name">YOUR NAME</p>
      <p class="person-role">Position</p>
    </div>
    <div class="contact-band">
      <ul class="contact-col">
        <li><svg viewBox="0 0 16 16"><path fill="#fff" d="M3 1l3 3-1.5 2a9 9 0 0 0 5.5 5.5L12 10l3 3-2 2C7 15 1 9 1 3z"/></svg>phone number</li>
        <li><svg viewBox="0 0 16 16"><rect x="1" y="3" width="14" height="10" fill="none" stroke="#fff" stroke-width="1.5"/><path d="M1 3l7 6 7-6" fill="none" stroke="#fff" stroke-width="1.5"/></svg>info@summitcapital.com</li>
      </ul>
      <ul class="contact-col">
        <li><svg viewBox="0 0 16 16"><circle cx="8" cy="8" r="6.5" fill="none" stroke="#fff" stroke-width="1.4"/><ellipse cx="8" cy="8" rx="3" ry="6.5" fill="none" stroke="#fff" stroke-width="1.2"/><path d="M1.5 8h13" stroke="#fff" stroke-width="1.2"/></svg>summitcapital.com</li>
        <li><svg viewBox="0 0 16 16"><path fill="#fff" d="M8 1a5 5 0 0 1 5 5c0 4-5 9-5 9S3 10 3 6a5 5 0 0 1 5-5zm0 3a2 2 0 1 0 0 4 2 2 0 0 0 0-4z"/></svg>office address</li>
      </ul>
    </div>
  </section>

  <section class="card card--back" aria-label="Card back">
    <div class="card__texture"></div>
    <div class="back__logo">
      <span class="logo-mark"></span>
      <span class="logo-name">Summit Capital</span>
    </div>
    <ul class="contact-col back__address">
      <li><svg viewBox="0 0 16 16"><path fill="#fff" d="M8 1a5 5 0 0 1 5 5c0 4-5 9-5 9S3 10 3 6a5 5 0 0 1 5-5zm0 3a2 2 0 1 0 0 4 2 2 0 0 0 0-4z"/></svg>office address</li>
    </ul>
    <div class="contact-band back__band">
      <ul class="contact-col">
        <li><svg viewBox="0 0 16 16"><path fill="#fff" d="M3 1l3 3-1.5 2a9 9 0 0 0 5.5 5.5L12 10l3 3-2 2C7 15 1 9 1 3z"/></svg>phone number</li>
        <li><svg viewBox="0 0 16 16"><rect x="1" y="3" width="14" height="10" fill="none" stroke="#fff" stroke-width="1.5"/><path d="M1 3l7 6 7-6" fill="none" stroke="#fff" stroke-width="1.5"/></svg>info@summitcapital.com</li>
      </ul>
    </div>
  </section>

</body>
</html>
```